Business Card (double-sided) and Stationary Design for dental office

1) Business Card Design: We need a business card design for a dental specialty office.
Texts should contain:
The name of our office "Brindle Oaks Orthodontics"
Tagline: "Specialist in Orthodontic and Maxillofacial Orthopedics"
Tag line: "Creating "Tolvering" smiles for Children and Adults"
Doctor name: "Doctor Name"
Office Address:
"123 Street Name
City, State Zip code"
Office email address: office@brindleoaksortho.com
Website: www.brindleoaksortho.com

We will provide the full office address once the design is selected
Theme: beach, paradise, coastal, wave
We would like to have some creativity in design. Some acceptable ideas: front page: logo and office name. Back page: more detail information, and map to office in form of an island. Please see sample from our other location, but you DON'T HAVE TO USE OR COPY THE SAME CONCEPT.

IF POSSIBLE, PLEASE SUBMIT AT LEAST TWO CONCEPTS: ONE WITH THE BACK LOOKING SIMILAR TO WHAT IS IN THE SAMPLE, AND ONE DIFFERENT.

Color: designer to choose. We have different shade of blues and sand color in our office. Please see logo.

2) Please also design a matching set of stationary that compliment the business card and our logo.

Target Market(s)

Dental

Contact Information for Business Card

See descriptions

Font styles to use
Other font styles liked:
• Matching texts in logo

Colors
0054AA
0677BA
7BADD7
CADEEF
E8F1F8
0094D4
00A9DD
6FCCEA
C7EBF8
E9F6FB
00AB8E
00BBA5
67D7C9
C6EFE9
E9F9F6

Requirements
Must have
• Double-sided
Nice to have
• Beach coastal theme
Should not have
• Any shape or drawing of of tooth or teeth. We don’t need these. You don't necessarily have to just cut and paste the logo art and text as a whole, you have the liberty to rearrange the text.

```html
<!DOCTYPE html>
<html lang="en">
<head>
<meta charset="utf-8">
<title>Brindle Oaks Orthodontics – Business Card</title>
<link href="https://fonts.googleapis.com/css2?family=Ubuntu:wght@500&family=Roboto:wght@400;700&family=Kalam:wght@700&display=swap" rel="stylesheet">
<style>
  :root{
    --bg:#e4e4e4;
    --card:#ffffff;
    --teal-dark:#3a8aa0;
    --teal-mid:#4f9db3;
    --mint:#67c9b8;
    --text:#3c3c3c;
    --wash:#e9f4f6;
    --brown:#4a2618;
    --sky:#69c2f3;
    --sea:#1aa3dd;
    --sand:#f2b866;
    --island:#f3c978;
    --palm:#7cc23a;
  }
  *{margin:0;padding:0;box-sizing:border-box}
  html,body{width:1200px;height:1200px;overflow:hidden;background:var(--bg)}
  .card{position:absolute;left:262px;width:686px;height:392px;border-radius:20px;overflow:hidden}
  .card-front{top:165px;background:linear-gradient(110deg,var(--card) 55%,var(--wash) 100%)}
  .card-back{top:653px}

  .front-tab{position:absolute;left:0;top:239px;width:10px;height:101px;background:var(--teal-dark);border-radius:0 6px 6px 0}
  .front-halo{position:absolute;left:358px;top:88px;width:380px;height:380px;border-radius:50%;background:#dcedf0;opacity:.6}
  .brand{position:absolute;left:55px;top:52px;width:260px;text-align:center}
  .brand-dot{width:100px;height:100px;border-radius:50%;background:var(--teal-mid);margin:0 auto 14px}
  .brand-name{font:500 34px/1 "Ubuntu",sans-serif;color:var(--teal-dark);white-space:nowrap;border-bottom:2px solid var(--mint);padding-bottom:2px}
  .brand-tag{font:500 12.5px/1.4 "Ubuntu",sans-serif;color:var(--mint);letter-spacing:1px;white-space:nowrap}

  .contact{position:absolute;left:55px;top:236px;list-style:none;font:400 16px/19.5px "Roboto",sans-serif;color:var(--text)}
  .contact li{display:flex;align-items:flex-start;gap:8px}
  .contact li.addr{margin-bottom:4px}
  .contact svg{width:13px;height:13px;margin-top:3px;flex:none;fill:var(--teal-dark)}
  .doctor{position:absolute;left:441px;top:274px;font:700 23px/1 "Roboto",sans-serif;color:var(--teal-mid);letter-spacing:.3px}

  .beach-scene{position:absolute;inset:0;background:linear-gradient(180deg,#7fcff6 0%,var(--sky) 38%,var(--sea) 48%,#3db6ea 62%,var(--sand) 75%,#eaa04e 100%)}
  .island-scene{position:absolute;left:330px;top:20px;width:356px;height:372px;
    background:
      radial-gradient(ellipse 40% 30% at 92% 45%,rgba(124,194,58,.85),rgba(124,194,58,0) 100%),
      radial-gradient(ellipse 22% 28% at 58% 28%,rgba(176,110,90,.85),rgba(176,110,90,0) 100%),
      radial-gradient(ellipse 55% 18% at 50% 48%,var(--island),rgba(243,201,120,0) 100%),
      radial-gradient(ellipse 55% 30% at 78% 95%,rgba(250,210,150,.9),rgba(250,210,150,0) 100%)}
  .back-brand{position:absolute;left:90px;top:40px;width:250px;text-align:center}
  .back-brand .brand-dot{width:74px;height:74px;background:var(--brown);margin-bottom:10px}
  .back-brand .brand-name{font-size:26px;color:var(--brown);border-bottom:1.5px solid var(--brown)}
  .back-brand .brand-tag{font-size:10px;color:var(--brown);letter-spacing:.8px}

  .appointment{position:absolute;left:31px;top:183px;width:429px;height:118px;border-radius:10px;background:rgba(255,255,255,.93);box-shadow:0 4px 12px rgba(0,0,0,.12);padding:20px 18px 0 17px;font-family:"Roboto",sans-serif;color:#2b1a12}
  .appointment h2{font-size:16px;font-weight:700;margin-bottom:14px}
  .field-row{display:flex;align-items:flex-end;font-size:15px;margin-bottom:12px}
  .field-line{flex:1;border-bottom:1px dotted #555;height:13px;margin:0 2px}
  .field-line.short{flex:1.3}

  .taglines{position:absolute;left:32px;top:322px;width:440px;text-align:center;font-family:"Kalam",cursive;color:var(--brown);font-weight:700;white-space:nowrap}
  .tag-one{font-size:15.5px;line-height:1.2;border-bottom:1.5px solid var(--brown);display:inline-block;padding:0 6px}
  .tag-two{font-size:17px;line-height:1.3;letter-spacing:-.2px}
</style>
</head>
<body>
  <section class="card card-front">
    <div class="front-halo"></div>
    <div class="front-tab"></div>
    <div class="brand">
      <div class="brand-dot"></div>
      <div class="brand-name">Brindle Oaks</div>
      <div class="brand-tag">Pediatric Dentistry &amp; Orthodontics</div>
    </div>
    <ul class="contact">
      <li class="addr"><svg viewBox="0 0 12 12"><path d="M6 0a4 4 0 0 0-4 4c0 3 4 8 4 8s4-5 4-8a4 4 0 0 0-4-4zm0 5.6A1.6 1.6 0 1 1 6 2.4a1.6 1.6 0 0 1 0 3.2z"/></svg><span>123 Street Name<br>City, State Zip code</span></li>
      <li><svg viewBox="0 0 12 12"><path d="M2.4 0.6l2 2.2-1.1 1.5a7 7 0 0 0 4.4 4.4l1.5-1.1 2.2 2-1.4 1.8C5 11 1 7 0.6 2z"/></svg><span>555-014-2277</span></li>
      <li><svg viewBox="0 0 12 12"><path d="M0 2.5h12v7H0zM0.8 3l5.2 3.6L11.2 3"/></svg><span>office@brindleoaksortho.com</span></li>
      <li><svg viewBox="0 0 12 12"><circle cx="6" cy="6" r="5.5"/></svg><span>www.brindleoaksortho.com</span></li>
    </ul>
    <div class="doctor">DANA WHITFIELD</div>
  </section>

  <section class="card card-back">
    <div class="beach-scene" role="img" aria-label="Illustrated sky with clouds, blue sea and sandy shore"></div>
    <div class="island-scene" role="img" aria-label="Illustrated sandy island with palm trees and a rocky peak, and a small hand-drawn street map to the office on the beach"></div>
    <div class="back-brand">
      <div class="brand-dot"></div>
      <div class="brand-name">Brindle Oaks</div>
      <div class="brand-tag">Pediatric Dentistry &amp; Orthodontics</div>
    </div>
    <div class="appointment">
      <h2>SEE YOU AT YOUR NEXT APPOINTMENT!</h2>
      <div class="field-row">For<span class="field-line"></span></div>
      <div class="field-row">Date<span class="field-line short"></span>Time<span class="field-line"></span></div>
    </div>
    <div class="taglines">
      <div class="tag-one">Specialist in Orthodontic &amp; Maxillofacial Orthopedics</div>
      <div class="tag-two">Creating "Tolvering" smiles for Children &amp; Adults</div>
    </div>
  </section>
</body>
</html>
```